Luxury Business Card Design for High-End Window Treatments

Gilded Slatworks
Custom Plantation Shutters & Architectural Shading Systems

⸻

BACK

Daniel Trevick
Owner

Custom Interior & Exterior Window Treatments

919-555-0148
gildedslatworks.com

I have included a picture that I’m hoping we can use on the back, but I’m also wondering if you can get rid of the ladder? Should we get rid of shutters , shades and blinds underneath Gilded Slatworks?

Target Market(s)

High-end residential homeowners, custom home builders, architects, interior designers, and luxury renovation clients seeking premium plantation shutters and motorized architectural shading systems.

Industry/Entity Type

Custom Window treatments

Contact Information for Business Card

Front Gilded Slatworks Custom Plantation Shutters Motorized Architectural Shading Systems BACK Daniel Trevick Owner 919-555-0148 GildedSlatworks.com Custom Interior & Exterior Window Treatments By Appointment

Requirements
Nice to have
• Not 100% sure on nice to halves or the color but you can definitely check out my website to get a better understanding of what I’m trying to do

```html
<!DOCTYPE html>
<html lang="en">
<head>
<meta charset="utf-8">
<title>Gilded Slatworks – Business Cards</title>
<link rel="stylesheet" href="https://fonts.googleapis.com/css2?family=Montserrat:wght@300;400&family=Playfair+Display:wght@600&family=Lora:wght@500&display=swap">
<style>
  :root {
    --canvas: #e6e5e8;
    --card-black: #000000;
    --cream: #f1ebdc;
    --name-gold: #b9a45a;
    --tagline-yellow: #efd35a;
    --appointment-gold: #d8bc4e;
    --stripe-olive: #8d8a3e;
    --photo-sky: #7faedb;
    --photo-house: #4a4f55;
    --photo-lawn: #5a6b3a;
  }
  * { margin: 0; padding: 0; box-sizing: border-box; }
  html, body { width: 1200px; height: 1108px; overflow: hidden; background: var(--canvas); }
  .card {
    position: absolute;
    background: var(--card-black);
    overflow: hidden;
  }
  .card--contact { left: 222px; top: 51px; width: 786px; height: 480px; }
  .card--brand { left: 220px; top: 577px; width: 788px; height: 463px; }

  .photo-panel { position: absolute; inset: 0; }

  .wordmark {
    position: absolute;
    font-family: "Montserrat", sans-serif;
    font-weight: 300;
    color: var(--cream);
    text-align: center;
    line-height: 1.05;
  }
  .card--contact .wordmark { left: 40px; top: 62px; width: 210px; font-size: 34px; }
  .card--brand .wordmark { left: 0; top: 128px; width: 100%; font-size: 66px; }

  .tagline {
    position: absolute;
    font-family: "Lora", serif;
    font-weight: 500;
    color: var(--tagline-yellow);
    text-align: center;
    word-spacing: 0.45em;
  }
  .card--contact .tagline { left: 40px; top: 152px; width: 210px; font-size: 16px; }
  .card--brand .tagline { left: 0; top: 326px; width: 100%; font-size: 31px; }

  .contact-block { position: absolute; left: 38px; top: 210px; font-family: "Montserrat", sans-serif; color: var(--cream); }
  .person-name { font-family: "Playfair Display", serif; font-weight: 600; font-size: 29px; color: var(--name-gold); line-height: 1.1; }
  .person-role { font-size: 17px; margin-top: 2px; }
  .service-line { font-size: 17px; line-height: 1.3; margin-top: 20px; }
  .contact-list { list-style: none; margin-top: 20px; }
  .contact-list li { display: flex; align-items: center; gap: 10px; font-size: 17.5px; height: 29px; }
  .contact-list svg { width: 19px; height: 19px; flex: none; }
  .appointment { color: var(--appointment-gold); font-size: 17.5px; margin-top: 13px; }
</style>
</head>
<body>

<section class="card card--contact">
  <svg class="photo-panel" width="786" height="480" viewBox="0 0 786 480">
    <defs>
      <linearGradient id="photoTone" x1="0" y1="0" x2="0" y2="1">
        <stop offset="0" stop-color="var(--photo-sky)"/>
        <stop offset="0.35" stop-color="#c9c6bd"/>
        <stop offset="0.6" stop-color="var(--photo-house)"/>
        <stop offset="1" stop-color="var(--photo-lawn)"/>
      </linearGradient>
    </defs>
    <polygon role="img" aria-label="Photo of a home's back porch with exterior shades and lawn chairs" points="476,0 786,0 786,480 345,480" fill="url(#photoTone)"/>
    <polygon points="464,0 476,0 357,480 345,480" fill="var(--stripe-olive)"/>
  </svg>

  <div class="wordmark">Gilded<br>Slatworks</div>
  <div class="tagline">Shutters Shades Blinds</div>

  <div class="contact-block">
    <div class="person-name">Daniel Trevick</div>
    <div class="person-role">Owner</div>
    <div class="service-line">Custom Interior &amp; Exterior<br>Window Treatments</div>
    <ul class="contact-list">
      <li>
        <svg viewBox="0 0 20 20" aria-hidden="true"><path d="M2 7c0-2 3-3 8-3s8 1 8 3v1h-4V6.5H6V8H2z" fill="var(--name-gold)"/><rect x="4" y="9" width="12" height="8" rx="1" fill="var(--name-gold)"/><circle cx="10" cy="13" r="2" fill="var(--card-black)"/></svg>
        919-555-0148
      </li>
      <li>
        <svg viewBox="0 0 20 20" aria-hidden="true"><circle cx="10" cy="10" r="8" fill="var(--name-gold)"/><path d="M5 7c2 0 3 1 3 3s2 2 2 4l-1 3M12 4c0 2 2 3 4 3" stroke="var(--card-black)" stroke-width="1.6" fill="none"/></svg>
        GildedSlatworks.com
      </li>
    </ul>
    <div class="appointment">By Appointment</div>
  </div>
</section>

<section class="card card--brand">
  <div class="wordmark">Gilded<br>Slatworks</div>
  <div class="tagline">Shutters Shades Blinds</div>
</section>

</body>
</html>
```